Health Care Company with Logo Needs Business Cards designed

We are a luxury behavioral health company looking for business cards design we already have a logo and are looking for someone to design a sophisticated luxurious looking business card. Please note that Card design should be captivating just like the logo and also encompass the logo color

Industry/Entity Type

Healthcare

Contact Information for Business Card

Logo,company name, tagline, my name and title, contact details, and physical address

```html
<!DOCTYPE html>
<html lang="en">
<head>
<meta charset="utf-8">
<title>Northwind Mind Care — Business Cards</title>
<link href="https://fonts.googleapis.com/css2?family=Archivo:wght@700;800&family=Arimo:wght@400;700&display=swap" rel="stylesheet">
<style>
  :root {
    --bg: #e9e9ea;
    --purple: #7a3592;
    --purple-deep: #6a2c86;
    --purple-light: #8a44a3;
    --blue: #1aa3e0;
    --orange: #ef8a1e;
    --white: #ffffff;
    --grey-text: #4a4a4a;
  }
  * { box-sizing: border-box; margin: 0; padding: 0; }
  html, body { width: 1200px; height: 802px; overflow: hidden; }
  body {
    background: var(--bg);
    display: flex;
    align-items: center;
    justify-content: center;
    gap: 50px;
  }
  .card {
    position: relative;
    width: 525px;
    height: 300px;
    border-radius: 3px;
    overflow: hidden;
    box-shadow: 0 8px 22px rgba(0,0,0,.18);
  }

  /* Front */
  .card--front { background: var(--white); }
  .front-band {
    position: absolute;
    left: 0; bottom: 0;
    width: 100%; height: 160px;
  }
  .front-mark {
    position: absolute;
    right: 22px; top: 22px;
    width: 78px; height: 78px;
    background: var(--orange);
  }
  .brand {
    position: absolute;
    left: 34px; top: 40px;
    display: flex;
    align-items: center;
    gap: 12px;
  }
  .brand__square {
    width: 34px; height: 34px;
    background: var(--orange);
    flex: none;
  }
  .brand__name {
    font-family: "Archivo", sans-serif;
    font-weight: 800;
    font-size: 27px;
    line-height: 1;
    color: var(--purple);
    letter-spacing: -0.2px;
    white-space: nowrap;
  }
  .brand__tagline {
    font-family: "Archivo", sans-serif;
    font-weight: 700;
    font-size: 8.5px;
    letter-spacing: 2.3px;
    text-transform: uppercase;
    color: var(--blue);
    margin-top: 5px;
    white-space: nowrap;
  }
  .person {
    position: absolute;
    left: 80px; top: 100px;
    font-family: "Arimo", sans-serif;
  }
  .person__name {
    font-weight: 700;
    font-size: 20px;
    color: var(--blue);
  }
  .person__title {
    font-size: 14px;
    color: var(--grey-text);
    margin-top: 2px;
  }
  .contact {
    position: absolute;
    left: 80px; top: 172px;
    list-style: none;
    font-family: "Arimo", sans-serif;
    font-size: 14.5px;
    color: var(--white);
  }
  .contact li {
    display: flex;
    align-items: center;
    gap: 10px;
    height: 24px;
    white-space: nowrap;
  }
  .contact svg { width: 13px; height: 13px; flex: none; }
  .contact .no-icon { padding-left: 23px; }

  /* Back */
  .card--back {
    background: linear-gradient(135deg, var(--purple-light) 0%, var(--purple) 50%, var(--purple-deep) 100%);
    display: flex;
    align-items: center;
    justify-content: center;
  }
  .card--back .brand { position: static; }
  .card--back .brand__name { color: var(--white); font-size: 31px; }
  .card--back .brand__tagline { font-size: 9.5px; letter-spacing: 2.6px; }
  .card--back .brand__square { width: 40px; height: 40px; }
</style>
</head>
<body>

  <section class="card card--front" aria-label="Business card front">
    <svg class="front-band" viewBox="0 0 525 160" preserveAspectRatio="none" aria-hidden="true">
      <polygon points="0,30 390,30 420,0 525,0 525,160 0,160" fill="var(--purple)"/>
    </svg>
    <span class="front-mark" aria-hidden="true"></span>

    <div class="brand">
      <span class="brand__square"></span>
      <div>
        <div class="brand__name">Northwind Mind Care</div>
        <div class="brand__tagline">Steady care for every season of life</div>
      </div>
    </div>

    <div class="person">
      <div class="person__name">Marcus Hale</div>
      <div class="person__title">Manager</div>
    </div>

    <ul class="contact">
      <li>
        <svg viewBox="0 0 16 16" aria-hidden="true"><path fill="#fff" d="M4 1.5l2.2 3-1.3 1.6a9 9 0 0 0 5 5l1.6-1.3 3 2.2-1.2 2.4C7.5 14.6 1.4 8.5 1.6 2.7z"/></svg>
        <span>555-018-7342</span>
      </li>
      <li>
        <svg viewBox="0 0 16 16" aria-hidden="true"><rect x="1.5" y="3.5" width="13" height="9" fill="none" stroke="#fff" stroke-width="1.6"/><path d="M1.5 3.5l6.5 5 6.5-5" fill="none" stroke="#fff" stroke-width="1.6"/></svg>
        <span>hello@northwindcare.com</span>
      </li>
      <li>
        <svg viewBox="0 0 16 16" aria-hidden="true"><circle cx="8" cy="8" r="6.5" fill="none" stroke="#fff" stroke-width="1.5"/><ellipse cx="8" cy="8" rx="2.8" ry="6.5" fill="none" stroke="#fff" stroke-width="1.2"/><path d="M1.5 8h13M2.8 4.6h10.4M2.8 11.4h10.4" stroke="#fff" stroke-width="1.1"/></svg>
        <span>www.northwindcare.com</span>
      </li>
      <li class="no-icon">Your address, city, state, ZIP 0000</li>
    </ul>
  </section>

  <section class="card card--back" aria-label="Business card back">
    <div class="brand">
      <span class="brand__square"></span>
      <div>
        <div class="brand__name">Northwind Mind Care</div>
        <div class="brand__tagline">Steady care for every season of life</div>
      </div>
    </div>
  </section>

</body>
</html>
```